Oil Field Service company needs professional business cards

Looking to clean up our current company business cards and look a little more professional. Brenwick Casing Services is a US based company that services the oil field. We deal with engineers, managers and oil rigs....................................................................................................................................................................................................................................................................................................................................................................................................

Target Market(s)

Oil and Gas professionals

Industry/Entity Type

Oil And Gas

Contact Information for Business Card

See attached photo as example

Font styles to use
Sans Serif

Colors
ec1f27

Requirements
Must have
• Company Logo, Name, Title, Cell, Office, Fax, Email.
• See attached photo
Nice to have
• External CRT, Internal CRT, Casing Crews, Torque Turn, Laydown Machine
Should not have
• Do not introduce any new pictures and keep it professional looking

```html
<!DOCTYPE html>
<html lang="en">
<head>
<meta charset="utf-8">
<title>Brenwick Casing Services – Business Card</title>
<link href="https://fonts.googleapis.com/css2?family=Open+Sans:ital,wght@0,400;0,600;0,700;1,600&display=swap" rel="stylesheet">
<style>
  :root {
    --canvas: #000000;
    --card: #333438;
    --brand-slate: #4b5662;
    --brand-red: #ec1f27;
    --divider: #6a1f22;
    --text-light: #ffffff;
    --text-soft: #e6e6e6;
  }
  * { margin: 0; padding: 0; box-sizing: border-box; }
  html, body {
    width: 1200px; height: 900px; overflow: hidden;
    background: var(--canvas);
    font-family: "Open Sans", Arial, sans-serif;
  }
  .canvas { position: relative; width: 1200px; height: 900px; }
  .card {
    position: absolute; top: 271px;
    width: 457px; height: 281px;
    background: var(--card);
    border-radius: 14px;
  }
  .card--front { left: 137px; }
  .card--back { left: 626px; }

  .brand {
    position: absolute;
    display: flex; align-items: center; gap: 8px;
    color: var(--brand-slate);
    font-weight: 700;
    text-transform: uppercase;
    line-height: 1.1;
  }
  .brand__dot { flex: none; border-radius: 50%; background: var(--brand-red); }
  .brand--front { left: 24px; top: 104px; width: 186px; font-size: 17px; letter-spacing: 0.06em; }
  .brand--front .brand__dot { width: 12px; height: 12px; }
  .brand--back { left: 0; right: 0; top: 110px; justify-content: center; font-size: 31px; letter-spacing: 0.08em; gap: 14px; }
  .brand--back .brand__dot { width: 20px; height: 20px; }
  .brand__name small { display: block; font-size: inherit; }

  .divider {
    position: absolute; left: 220px; top: 69px;
    width: 1px; height: 122px; background: var(--divider);
  }
  .contact { position: absolute; left: 238px; top: 67px; color: var(--text-light); }
  .contact__name { font-size: 15px; font-weight: 600; line-height: 20px; }
  .contact__title { font-size: 12px; line-height: 15px; color: var(--text-soft); }
  .contact__list { list-style: none; margin-top: 24px; }
  .contact__item {
    display: flex; align-items: center; gap: 7px;
    font-size: 12.5px; line-height: 16.5px; color: var(--text-soft);
  }
  .contact__item svg { width: 9px; height: 9px; fill: var(--text-soft); flex: none; }

  .services {
    position: absolute; left: 0; right: 0; top: 227px;
    text-align: center; color: var(--text-light);
    font-size: 14px; font-style: italic; font-weight: 600;
  }
</style>
</head>
<body>
<div class="canvas">
  <section class="card card--front">
    <div class="brand brand--front">
      <span class="brand__dot"></span>
      <span class="brand__name">Brenwick<small>Casing Services</small></span>
    </div>
    <div class="divider"></div>
    <div class="contact">
      <p class="contact__name">Cole Marrington</p>
      <p class="contact__title">Area Manager</p>
      <ul class="contact__list">
        <li class="contact__item">
          <svg viewBox="0 0 10 10"><path d="M2 0.5l1.8 2-1 1.1c.6 1.3 1.5 2.2 2.7 2.8l1.1-1 2 1.7-1 1.9C4.3 9 1 5.7.1 1.5z"/></svg>
          (405) 218-4400
        </li>
        <li class="contact__item">
          <svg viewBox="0 0 10 10"><path d="M3 0h4a1 1 0 0 1 1 1v8a1 1 0 0 1-1 1H3a1 1 0 0 1-1-1V1a1 1 0 0 1 1-1zm0 1.5v6h4v-6z"/></svg>
          (405) 377-5921
        </li>
        <li class="contact__item">
          <svg viewBox="0 0 10 10"><path d="M2.5 0h4l1 1v2h1.5a1 1 0 0 1 1 1v5H0V4a1 1 0 0 1 1-1h1.5zm1 1v2h3V1zM5 5h3v1H5zm0 2h3v1H5z"/></svg>
          (405) 218-4419
        </li>
        <li class="contact__item">
          <svg viewBox="0 0 10 10"><path d="M0 2h10v6H0zm1 .6L5 5.5l4-2.9V2.4H1z"/></svg>
          cole.marrington@mailbox.com
        </li>
      </ul>
    </div>
    <p class="services">Laydown Machine | Casing Crew | Mud Tool | Torque Turn</p>
  </section>

  <section class="card card--back">
    <div class="brand brand--back">
      <span class="brand__dot"></span>
      <span class="brand__name">Brenwick<small>Casing Services</small></span>
    </div>
  </section>
</div>
</body>
</html>
```